Business Card Design

We need a new business card design for a company based in Ashmere, OK. We provide business consulting services in the information technology / services space. We like variations of the color blue, aqua, black, light tan, and white. Would like "cool" tones. The design should clearly communicate professionalism. Think outside the box - we don't want something "typical". Our company name is "Halvery Consulting, LLC".
Updates

Thank you all for your submissions. We have seen some very creative and inspired designs. We have made a decision and will be moving forward with that design. Appreciate all of the hard work.

Industry/Entity Type

Information Technology

Contact Information for Business Card

Megan Halvery Strube
218 West Birchfold Ridge Dr.
Ashmere, OK 76418

```html
<!DOCTYPE html>
<html lang="en">
<head>
<meta charset="utf-8">
<title>Halvery Consulting, LLC — Business Card</title>
<link rel="stylesheet" href="https://fonts.googleapis.com/css2?family=Open+Sans:wght@400&family=Ubuntu:wght@400&display=swap">
<style>
  :root {
    --backdrop: #2b2c30;
    --card: #f7f8fa;
    --brand-blue: #3d8ee0;
    --brand-deep: #1e64b8;
    --band-light: #3f93e2;
    --band-dark: #1a5fb3;
    --ink: #2a2c31;
    --rule: #2f7fd4;
  }
  * { margin: 0; padding: 0; box-sizing: border-box; }
  html, body {
    width: 1200px;
    height: 960px;
    overflow: hidden;
    background: var(--backdrop);
  }
  .stage {
    width: 1200px;
    height: 960px;
    display: flex;
    align-items: center;
    justify-content: center;
  }
  .business-card {
    position: relative;
    width: 840px;
    height: 480px;
    background: var(--card);
    overflow: hidden;
    box-shadow: 0 18px 40px rgba(0, 0, 0, 0.45);
  }
  .brand {
    position: absolute;
    top: 58px;
    right: 60px;
    display: flex;
    align-items: center;
    gap: 22px;
  }
  .brand-mark {
    width: 84px;
    height: 84px;
    border-radius: 50%;
    background: var(--brand-deep);
    flex: none;
  }
  .company-name {
    font-family: "Ubuntu", sans-serif;
    font-weight: 400;
    font-size: 40px;
    color: var(--brand-blue);
    white-space: nowrap;
  }
  .person-name {
    position: absolute;
    top: 168px;
    right: 60px;
    font-family: "Ubuntu", sans-serif;
    font-weight: 400;
    font-size: 34px;
    color: var(--brand-blue);
  }
  .divider {
    position: absolute;
    top: 236px;
    left: 60px;
    right: 60px;
    height: 2px;
    background: var(--rule);
  }
  .contact {
    position: absolute;
    top: 262px;
    left: 60px;
    font-family: "Open Sans", sans-serif;
    font-size: 22px;
    color: var(--ink);
    line-height: 1.75;
  }
  .contact-row {
    display: flex;
    align-items: center;
    gap: 28px;
  }
  .contact-item {
    display: inline-flex;
    align-items: center;
    gap: 9px;
    white-space: nowrap;
  }
  .icon {
    width: 22px;
    height: 22px;
    flex: none;
  }
  .accent-band {
    position: absolute;
    left: 0;
    right: 0;
    bottom: 0;
    height: 74px;
    background: linear-gradient(90deg, var(--band-dark), var(--band-light) 50%, var(--band-dark));
  }
</style>
</head>
<body>
  <main class="stage">
    <article class="business-card">
      <header class="brand">
        <span class="company-name">Halvery Consulting, LLC</span>
        <span class="brand-mark" aria-hidden="true"></span>
      </header>

      <p class="person-name">Megan Halvery Strube</p>

      <div class="divider"></div>

      <section class="contact">
        <div class="contact-row">
          <span class="contact-item">
            <svg class="icon" viewBox="0 0 24 24" aria-hidden="true">
              <path fill="var(--brand-deep)" d="M6.6 10.8a15.1 15.1 0 0 0 6.6 6.6l2.2-2.2a1 1 0 0 1 1-.25 11.4 11.4 0 0 0 3.6.57 1 1 0 0 1 1 1V20a1 1 0 0 1-1 1A17 17 0 0 1 3 4a1 1 0 0 1 1-1h3.5a1 1 0 0 1 1 1c0 1.25.2 2.450.57 3.57a1 1 0 0 1-.25 1z"/>
            </svg>
            580-555-0142
          </span>
          <span class="contact-item">
            <svg class="icon" viewBox="0 0 24 24" aria-hidden="true">
              <rect x="2.5" y="5" width="19" height="14" rx="1.5" fill="none" stroke="var(--brand-deep)" stroke-width="2"/>
              <path d="M3 6l9 7 9-7" fill="none" stroke="var(--brand-deep)" stroke-width="2"/>
            </svg>
            megan.strube@halverymail.com
          </span>
        </div>
        <div class="contact-row">
          <span class="contact-item">
            <svg class="icon" viewBox="0 0 24 24" aria-hidden="true">
              <path fill="var(--brand-deep)" d="M12 2a7 7 0 0 0-7 7c0 5.2 7 13 7 13s7-7.8 7-13a7 7 0 0 0-7-7zm0 9.5A2.5 2.5 0 1 1 12 6.5a2.5 2.5 0 0 1 0 5z"/>
            </svg>
            218 West Birchfold Ridge Dr. Ashmere, OK 76418
          </span>
        </div>
      </section>

      <div class="accent-band"></div>
    </article>
  </main>
</body>
</html>
```